Elegant Business Card for Technology Company

Client is a supplier of innovative industrial communications and automation equipment since 2002. This contest is to gather fresh ideas for a redesign of the existing business card. Client is looking for design that best communicates tagline "Industrial Networking and Computing Specialist".

Design submissions should look modern, clean, elegant and professional. It should not be cluttered. Use white as the primary colour. Orange and black as secondary colour. Refer to jpeg File 1 on the current design.

Fonts used by Client used include Arial Regular, Arial Black, Roboto Regular, Roboto Black and Lato.

The winning design will be sent for offset printing using super white 250gsm artcard paper (open for suggestions).

Target Market(s)

System Engineers, Project Managers, Purchasing Managers from companies providing engineering services for Smart Cities.

Industry/Entity Type

Information Technology

Contact Information for Business Card

Refer to PDF File 3 for Business Card Details. Priority of short contact information would be as follows Name > Job Title > Email > Mobile > Web > Tel > Fax > Business Address >UEN (UEN represents company registration number)

Font styles to use
Sans Serif

Colors
ffffff
f37122
000000
5c5c5c

Requirements
Must have
• Refer to AI File 2 (Company Logo) & PDF File 3 (Information on Namecard)
Should not have
• No QR codes
• No Social Media Icons
• Do not create full Black or Orange colour background

```html
<!DOCTYPE html>
<html lang="en">
<head>
<meta charset="utf-8">
<title>Veltrix Business Card</title>
<link rel="stylesheet" href="https://fonts.googleapis.com/css2?family=Roboto:wght@400;700;900&display=swap">
<style>
  :root {
    --white: #ffffff;
    --orange: #f37122;
    --black: #000000;
    --grey: #5c5c5c;
    --backdrop: #e7e7e7;
    --peach: #fde9dc;
  }
  * { margin: 0; padding: 0; box-sizing: border-box; }
  html, body { width: 1200px; height: 900px; overflow: hidden; }
  body {
    background: var(--backdrop);
    font-family: "Roboto", Arial, sans-serif;
    color: var(--black);
    position: relative;
  }
  .card {
    position: absolute;
    left: 260px;
    width: 680px;
    height: 388px;
    background: var(--white);
    box-shadow: 0 6px 18px rgba(0,0,0,.18);
    overflow: hidden;
  }
  .card--front { top: 48px; }
  .card--back { top: 464px; }

  /* front */
  .front-texture {
    position: absolute;
    right: 0; top: 0;
    width: 400px; height: 388px;
    background: radial-gradient(ellipse at 80% 30%, var(--peach) 0%, rgba(253,233,220,.45) 45%, rgba(255,255,255,0) 75%);
  }
  .brand {
    display: flex;
    align-items: center;
    gap: 14px;
  }
  .brand__dot {
    width: 46px; height: 46px;
    border-radius: 50%;
    background: var(--orange);
  }
  .brand__name {
    font-weight: 900;
    font-size: 58px;
    letter-spacing: 1px;
    color: var(--black);
    line-height: 1;
  }
  .card--front .brand {
    position: absolute;
    left: 150px; top: 88px;
  }
  .tagline {
    position: absolute;
    left: 0; right: 0; top: 196px;
    text-align: center;
    color: var(--orange);
    font-size: 17px;
    letter-spacing: .3px;
    text-transform: uppercase;
  }
  .services {
    position: absolute;
    left: 0; right: 0; top: 228px;
    list-style: none;
    text-align: center;
    font-size: 16px;
    line-height: 21px;
    color: var(--black);
  }

  /* back */
  .card--back .brand {
    position: absolute;
    left: 48px; top: 120px;
  }
  .card--back .brand__name { font-size: 50px; }
  .card--back .brand__dot { width: 40px; height: 40px; }
  .company {
    position: absolute;
    left: 48px; top: 188px;
    font-size: 15px;
    letter-spacing: .4px;
    color: var(--black);
  }
  .divider {
    position: absolute;
    left: 356px; top: 26px;
    width: 1px; height: 150px;
    background: var(--grey);
  }
  .contact {
    position: absolute;
    left: 376px; top: 26px;
  }
  .contact__name {
    font-weight: 900;
    font-size: 20px;
    letter-spacing: .5px;
  }
  .contact__title {
    color: var(--orange);
    font-size: 13px;
    letter-spacing: .8px;
    margin-bottom: 3px;
  }
  .contact__address {
    font-size: 13px;
    line-height: 16px;
    margin-bottom: 4px;
  }
  .contact__list { list-style: none; }
  .contact__list li {
    display: flex;
    align-items: center;
    gap: 8px;
    font-size: 13px;
    line-height: 17px;
  }
  .contact__list svg { width: 11px; height: 11px; flex: none; }
  .bands {
    position: absolute;
    left: 0; bottom: 0;
    width: 680px; height: 120px;
  }
  .uen {
    position: absolute;
    right: 16px; bottom: 92px;
    font-size: 14px;
    color: var(--white);
    letter-spacing: .4px;
  }
  .uen__label { color: var(--orange); font-weight: 700; }
</style>
</head>
<body>

<section class="card card--front">
  <div class="front-texture" role="img" aria-label="Soft orange dotted texture fading across the card"></div>
  <div class="brand">
    <span class="brand__dot"></span>
    <span class="brand__name">VELTRIX</span>
  </div>
  <p class="tagline">Industrial Networking and Computing Specialist</p>
  <ul class="services">
    <li>Industrial Ethernet / Wireless / Cellular</li>
    <li>Industrial and Embedded Computing</li>
    <li>Serial / Fieldbus Connectivity</li>
    <li>IP Video Surveillance</li>
    <li>Remote Automation</li>
  </ul>
</section>

<section class="card card--back">
  <div class="brand">
    <span class="brand__dot"></span>
    <span class="brand__name">VELTRIX</span>
  </div>
  <p class="company">VELTRIX ASIA PACIFIC PTE LTD</p>

  <div class="divider"></div>

  <div class="contact">
    <h1 class="contact__name">DANIEL KOH</h1>
    <p class="contact__title">SALES MANAGER</p>
    <p class="contact__address">22 Harbour Lane Tech Hub #05-12<br>(Block B), Singapore 408900</p>
    <ul class="contact__list">
      <li>
        <svg viewBox="0 0 12 12"><rect x="3" y="0.5" width="6" height="11" rx="1.2" fill="none" stroke="#f37122" stroke-width="1.3"/><circle cx="6" cy="9.4" r=".8" fill="#f37122"/></svg>
        +65 8123 4567
      </li>
      <li>
        <svg viewBox="0 0 12 12"><path d="M2.2 1l2 .2 1 2.6-1.3 1a7 7 0 0 0 3.3 3.3l1-1.3 2.6 1 .2 2A1.2 1.2 0 0 1 9.8 11 9 9 0 0 1 1 2.2 1.2 1.2 0 0 1 2.2 1z" fill="#f37122"/></svg>
        +65 6234 5670
      </li>
      <li>
        <svg viewBox="0 0 12 12"><rect x="3" y="1" width="6" height="3.5" fill="none" stroke="#f37122" stroke-width="1.2"/><rect x="1" y="4.5" width="10" height="5" rx="1" fill="#f37122"/><rect x="3" y="8" width="6" height="3" fill="#f37122"/></svg>
        +65 6234 5671
      </li>
      <li>
        <svg viewBox="0 0 12 12"><rect x="1" y="2.5" width="10" height="7" fill="none" stroke="#f37122" stroke-width="1.2"/><path d="M1 2.5l5 4 5-4" fill="none" stroke="#f37122" stroke-width="1.2"/></svg>
        sales@veltrix.com.sg
      </li>
      <li>
        <svg viewBox="0 0 12 12"><circle cx="6" cy="6" r="5" fill="none" stroke="#f37122" stroke-width="1.1"/><ellipse cx="6" cy="6" rx="2.2" ry="5" fill="none" stroke="#f37122" stroke-width="1"/><path d="M1 6h10" stroke="#f37122" stroke-width="1"/></svg>
        www.veltrix.com.sg
      </li>
    </ul>
  </div>

  <svg class="bands" viewBox="0 0 680 120" preserveAspectRatio="none" aria-hidden="true">
    <polygon points="0,102 450,44 680,8 680,24 450,58 0,120" fill="#f37122"/>
    <polygon points="478,40 680,0 680,34 470,66" fill="#f37122"/>
    <polygon points="490,2 680,-40 680,30 470,42" fill="#000000"/>
  </svg>
  <p class="uen"><span class="uen__label">UEN No:</span> 200209876K</p>
</section>

</body>
</html>
```